Tax Preparation flyer for LedgerVale Corp.

My Client would like a one page PDF flyer to promote upcoming tax season in Canada. This firm is affordable and all virtual. I have attached a copy of their logo and a word document with the proposed wording for the flyer. Please feel free to change if you have better suggestions.

Target Market(s)

individuals in canada

Colors
0054AA
0677BA
7BADD7
CADEEF
E8F1F8

```html
<!DOCTYPE html>
<html lang="en">
<head>
<meta charset="utf-8">
<title>LedgerVale Corp. – Tax Season Flyer</title>
<link href="https://fonts.googleapis.com/css2?family=Poppins:wght@300;400;500;600;700;800&display=swap" rel="stylesheet">
<style>
  :root{
    --blue:#1b9ad6;
    --slate:#416478;
    --ink:#333538;
    --text:#2e2f31;
    --panel:#e8f1f8;
    --white:#ffffff;
    --canvas:#e2e2e2;
  }
  *{box-sizing:border-box;margin:0;padding:0}
  html,body{width:1200px;height:1200px;overflow:hidden;background:var(--canvas)}
  body{position:relative;font-family:"Poppins",sans-serif;color:var(--text)}
  .flyer{position:absolute;left:213px;top:58px;width:1245px;height:1745px;background:var(--white);
    transform:scale(.6209);transform-origin:0 0;overflow:hidden}
  .abs{position:absolute}
  .shapes{position:absolute;left:0;top:0}
  .hero-photo{position:absolute;left:277px;top:339px;width:968px;height:543px;
    background:linear-gradient(90deg,#c9d0d6 0%,#eef2f5 30%,#f7f9fb 55%,#dfe5ea 80%,#c7ced4 100%)}
  .headline{right:43px;top:18px;font-size:142px;font-weight:700;color:var(--blue);line-height:1;letter-spacing:-2px}
  .subhead{right:43px;top:142px;font-size:52px;font-weight:500;color:var(--text);line-height:1.1}
  .intro{right:43px;top:214px;font-size:21px;font-weight:400;line-height:28.5px;text-align:right;color:var(--text)}
  .hl{color:var(--blue);font-weight:700}
  .meet{left:45px;top:900px;width:1160px;font-size:25px;line-height:33px;letter-spacing:.4px}
  .pricing-title{left:425px;top:968px;width:402px;text-align:center;font-size:46px;font-weight:700;color:var(--white)}
  .tier-head{height:50px;border-radius:6px;background:var(--ink);color:var(--white);display:flex;align-items:center;padding:0 8px 0 18px}
  .tier-name{font-size:35px;font-weight:700;line-height:1}
  .tier-price{margin-left:16px;background:var(--blue);border-radius:22px;padding:0 16px;height:40px;display:flex;align-items:center;font-size:36px;font-weight:500}
  .tier-unit{margin-left:auto;font-size:20px;line-height:23px;text-align:center;font-weight:300}
  .features{list-style:none;font-size:19px;line-height:27px}
  .features li{position:relative;padding-left:22px;margin-bottom:9px}
  .features li::before{content:"";position:absolute;left:0;top:6px;width:15px;height:15px;border-radius:50%;background:var(--blue)}
  .features li::after{content:"";position:absolute;left:4px;top:9px;width:6px;height:4px;border-left:2px solid var(--white);border-bottom:2px solid var(--white);transform:rotate(-45deg)}
  .tier-note{left:849px;top:1396px;font-size:18px;line-height:24px}
  .behind{left:0;width:1245px;top:1484px;text-align:center;font-size:29px;font-weight:700}
  .offer{left:129px;top:1532px;width:985px;height:36px;text-align:center;font-size:20px;line-height:36px;color:var(--white)}
  .contact-title{left:45px;top:1621px;font-size:35px;font-weight:700;color:var(--white)}
  .contact-item{top:1676px;height:40px;display:flex;align-items:center;gap:12px;font-size:22px;color:var(--white)}
  .brand{right:43px;top:1596px;text-align:right;font-size:60px;font-weight:700;color:var(--ink);line-height:1}
</style>
</head>
<body>
<main class="flyer">
  <div class="hero-photo" role="img" aria-label="Photo of a relaxed businessman meditating at his office desk by bright windows"></div>

  <svg class="shapes" width="1245" height="1745" viewBox="0 0 1245 1745" aria-hidden="true">
    <polygon points="0,0 117,0 352,339 0,339" fill="var(--blue)"/>
    <polygon points="0,70 122,70 280,339 127,882 0,882" fill="var(--slate)"/>
    <polygon points="280,339 687,882 127,882" fill="#6e7073" opacity=".75"/>
    <rect x="0" y="882" width="975" height="16" fill="var(--blue)"/>
    <rect x="975" y="882" width="270" height="16" fill="var(--ink)"/>
    <!-- pricing panel -->
    <path d="M425,985 L425,967 L445,967 Z" fill="var(--slate)"/>
    <rect x="42" y="985" width="1160" height="495" rx="15" fill="var(--panel)" stroke="#3a3c3f" stroke-width="2"/>
    <path d="M425,967 L827,967 C800,980 800,1029 760,1029 L492,1029 C452,1029 452,980 425,967 Z" fill="var(--blue)"/>
    <path d="M425,967 L445,967 C430,972 428,978 425,985 Z M827,967 L807,967 C822,972 824,978 827,985 Z" fill="var(--slate)"/>
    <line x1="427" y1="1047" x2="427" y2="1442" stroke="var(--ink)" stroke-width="2"/>
    <line x1="814" y1="1047" x2="814" y2="1442" stroke="var(--ink)" stroke-width="2"/>
    <line x1="164" y1="1377" x2="304" y2="1377" stroke="var(--blue)" stroke-width="5" stroke-linecap="round"/>
    <line x1="550" y1="1377" x2="690" y2="1377" stroke="var(--blue)" stroke-width="5" stroke-linecap="round"/>
    <line x1="948" y1="1377" x2="1088" y2="1377" stroke="var(--blue)" stroke-width="5" stroke-linecap="round"/>
    <!-- offer bar -->
    <rect x="133" y="1536" width="985" height="36" rx="4" fill="none" stroke="var(--ink)" stroke-width="2"/>
    <rect x="129" y="1532" width="985" height="36" rx="4" fill="var(--ink)"/>
    <!-- contact band -->
    <polygon points="0,1620 257,1620 297,1669 0,1669" fill="var(--blue)"/>
    <polygon points="540,1669 570,1669 640,1745 610,1745" fill="var(--blue)"/>
    <polygon points="0,1669 540,1669 610,1745 0,1745" fill="var(--ink)"/>
  </svg>

  <h1 class="abs headline">Relax!</h1>
  <h2 class="abs subhead">We’ve Got Your Taxes Covered!</h2>
  <p class="abs intro">It has never been easier to file your taxes.&nbsp; Our virtual tax office let’s you file from the<br>comfort of your home or office and know that our tax expects have taken care of all<br>the work. Completely virtual, forms are signed via <span class="hl">SignSure</span> and you can upload<br>documents to us and receive documents from us in our <span class="hl">Secured Client Portal</span>.</p>

  <p class="abs meet">Need a tax review or have questions, our tax experts are available on <span class="hl">MeetLine, TalkRoom or VidCall</span> for your convenience.</p>

  <div class="abs pricing-title">Pricing</div>

  <section class="abs tier" style="left:57px;top:1044px;width:357px">
    <div class="tier-head"><span class="tier-name">Basic</span><span class="tier-price">$95</span><span class="tier-unit">Per<br>return</span></div>
    <ul class="features" style="margin-top:14px">
      <li>Full tax preparation from start to finish by a tax expert</li>
      <li>RRSP, donations &amp; medical expenses</li>
      <li>ideal for newcomers, students &amp; seniors</li>
      <li>Maximum refund guranteed</li>
      <li>Audit representation (valued at $30)</li>
    </ul>
  </section>

  <section class="abs tier" style="left:443px;top:1044px;width:357px">
    <div class="tier-head" style="padding-left:8px"><span class="tier-name">Premium</span><span class="tier-price" style="margin-left:8px">$125</span><span class="tier-unit">Per<br>return</span></div>
    <ul class="features" style="margin-top:14px">
      <li>Full tax preparation from start to finish by a tax expert</li>
      <li>Emigrant tax return</li>
      <li>Final (deceased) tax return</li>
      <li>Claim industry specific deductions to lower tax owing</li>
      <li>Audit representation (valued at $30)</li>
    </ul>
  </section>

  <section class="abs tier" style="left:830px;top:1044px;width:357px">
    <div class="tier-head" style="padding-left:8px"><span class="tier-name">Business</span><span class="tier-price" style="margin-left:10px">$195</span><span class="tier-unit">Per<br>return</span></div>
    <ul class="features" style="margin-top:14px">
      <li>Full tax preparation from start to finish by a tax expert</li>
      <li>Business/self-employment income</li>
      <li style="margin-bottom:7px">Rental property*</li>
      <li style="margin-bottom:7px">Partnership income</li>
      <li style="margin-bottom:7px">Non-resident tax return</li>
      <li style="margin-bottom:7px">Trust action(T3)</li>
      <li>Audit representation (valued at $50)</li>
    </ul>
  </section>
  <p class="abs tier-note">* Fee included one rental property, or<br>one business</p>

  <p class="abs behind">Have you fallen behind <span style="color:var(--blue)">in your taxes</span>?</p>
  <p class="abs offer">File 3 or more years and receive a <span class="hl">20% discount</span>.&nbsp; We can file back to <span class="hl">2012</span>.</p>

  <div class="abs contact-title">Contact us:</div>
  <div class="abs contact-item" style="left:43px">
    <svg width="28" height="28" viewBox="0 0 28 28" aria-hidden="true"><circle cx="14" cy="14" r="13" fill="none" stroke="#fff" stroke-width="1.6"/><rect x="8" y="9.5" width="12" height="9" fill="none" stroke="#fff" stroke-width="1.4"/><path d="M8,9.5 L14,15 L20,9.5" fill="none" stroke="#fff" stroke-width="1.4"/></svg>
    <span>hello@ledgervale.ca</span>
  </div>
  <div class="abs contact-item" style="left:319px">
    <svg width="28" height="28" viewBox="0 0 28 28" aria-hidden="true"><circle cx="14" cy="14" r="13" fill="none" stroke="#fff" stroke-width="1.6"/><path d="M10,8 L12.5,8 L13.5,11 L12,12.3 C12.8,14 14,15.2 15.7,16 L17,14.5 L20,15.5 L20,18 C20,19 19,19.8 18,19.6 C13,18.8 9.2,15 8.4,10 C8.2,9 9,8 10,8 Z" fill="none" stroke="#fff" stroke-width="1.4"/></svg>
    <span>(877) 555-0148</span>
  </div>

  <div class="abs brand">LedgerVale<br>Corp.</div>
</main>
</body>
</html>
```